Podiatry clinic requires a modern revamp and editing of existing website.

I would like a fresh new look and updated information for my current business website. An easy to navigate site with prominent address and phone number for call to action. We are a podiatry clinic that focuses on general and sports podiatry.
I would like 4 pages; including Home page, About Us, Services & Contact.
www.brambleridgepodiatry.net

Target Market(s)

Active working professionals.

Industry/Entity Type

Medical

Coding

Coded - Design and coding required

Number of Pages Required

4 page

Font styles to use
Sans Serif

Colors
6b449b

Requirements
Must have
• A modern look with logo and active images; clean and uncluttered. Visible phone number and address for call to action.
• 4 pages - Home, About Us, Services, Contact.
• Home page - update address & service logos.
• About Us - update of personal information.
• Services - Revamp of existing page.
• Contact page to include Google map, email & phone number.
Nice to have
• Ability to add content easily; eg. a blog or adding video onto Home page.
• Link to Our Page page.

```html
<!DOCTYPE html>
<html lang="en">
<head>
<meta charset="utf-8">
<title>Bramble Ridge Podiatry</title>
<link rel="stylesheet" href="https://fonts.googleapis.com/css2?family=Raleway:wght@300;400;600;700&family=Roboto+Condensed:wght@300;400&family=Open+Sans:wght@400;600;700&display=swap">
<style>
:root{
  --purple:#553593;
  --purple-dark:#452a7e;
  --purple-soft:#d9d2ea;
  --green:#7cbb2b;
  --orange:#f07a22;
  --grey-bg:#efefef;
  --text:#555;
  --white:#fff;
  --badge-orange:#f2a33a;
  --badge-blue:#1f5fa8;
  --badge-green:#6fb52c;
  --badge-ink:#2f2f2f;
}
*{box-sizing:border-box;margin:0;padding:0}
html,body{width:1200px;height:3025px;overflow:hidden}
body{font-family:'Open Sans',sans-serif;color:var(--text);background:var(--white);position:relative}
h1,h2,h3,h4{font-weight:400}
.section{position:absolute;left:0;width:1200px}
.photo{position:absolute}

/* hero */
.hero{top:0;height:678px;background:linear-gradient(180deg,#2d2a33 0%,#6d5460 30%,#c78658 45%,#5b4c48 60%,#3a3a3e 100%);overflow:hidden}
.hero .photo{inset:0}
.brand{position:absolute;left:80px;top:22px;display:flex;align-items:center;gap:12px;font-family:'Raleway',sans-serif;font-weight:700;font-size:26px;color:var(--white)}
.brand-dot{width:44px;height:44px;border-radius:50%;background:var(--purple)}
.hero-contact{position:absolute;right:88px;top:36px;text-align:right;font-family:'Roboto Condensed',sans-serif;font-size:20px;color:var(--white);line-height:46px}
.hero-contact svg{vertical-align:-4px;margin-right:8px}
.hero-contact b{font-weight:400}
.hero-title{position:absolute;top:250px;width:100%;text-align:center;font-family:'Roboto Condensed',sans-serif;font-weight:300;font-size:80px;color:var(--white)}
.hero-rule{position:absolute;top:364px;left:410px;width:380px;height:2px;background:rgba(255,255,255,.8)}
.hero-sub{position:absolute;top:385px;width:100%;text-align:center;font-family:'Roboto Condensed',sans-serif;font-weight:300;font-size:38px;color:var(--white)}
.btn-book{position:absolute;top:466px;left:470px;width:252px;height:50px;background:var(--purple);color:var(--white);font-family:'Raleway',sans-serif;font-size:17px;display:flex;align-items:center;justify-content:center;border-radius:3px}

/* nav */
.main-nav{top:678px;height:60px;background:var(--purple);display:flex;padding-left:77px}
.main-nav a{color:var(--white);text-decoration:none;font-family:'Raleway',sans-serif;font-size:18px;display:flex;align-items:center;padding:0 32px}
.main-nav a.active{background:var(--green);padding:0 34px}

/* welcome */
.welcome{top:738px;height:360px}
.welcome .photo{left:0;top:0;width:155px;height:252px;background:linear-gradient(135deg,#e9d6cc,#d2a290 60%,#c44a3a)}
.welcome h1{position:absolute;top:52px;width:100%;text-align:center;font-family:'Raleway',sans-serif;font-weight:300;font-size:41px;color:#444}
.welcome h1 span{color:var(--purple);font-weight:400}
.welcome p{position:absolute;left:180px;width:840px;text-align:center;font-size:15px;line-height:26px;color:#666}
.welcome .p1{top:122px}.welcome .p2{top:196px}
.btn-pill{position:absolute;background:var(--purple);color:var(--white);border-radius:26px;font-family:'Raleway',sans-serif;display:flex;align-items:center;justify-content:center}
.welcome .btn-pill{top:266px;left:505px;width:190px;height:50px;font-size:21px}

/* enquiry */
.enquiry{top:1107px;left:77px;width:1046px;height:258px;background:var(--grey-bg);border-bottom:4px solid var(--purple);box-shadow:0 22px 26px -14px rgba(0,0,0,.35)}
.enquiry .foot{left:70px;top:24px;width:100px;height:190px;background:#cfcfcf;border-radius:50px 50px 40px 40px}
.enquiry .hands{right:20px;top:0;width:140px;height:254px;background:linear-gradient(135deg,#efefef 10%,#f0d0bd 40%,#d9a184)}
.enquiry .notch{position:absolute;left:505px;bottom:-16px;width:0;height:0;border-left:14px solid transparent;border-right:14px solid transparent;border-top:12px solid var(--purple)}
.enq-title{position:absolute;top:26px;width:100%;text-align:center;font-family:'Raleway',sans-serif;font-weight:400;font-size:39px;color:var(--orange)}
.enq-call{position:absolute;top:92px;width:100%;display:flex;justify-content:center;align-items:center;gap:14px;font-family:'Raleway',sans-serif;font-size:30px;color:var(--green)}
.enq-call b{font-family:'Open Sans',sans-serif;font-weight:700}
.enq-or{position:absolute;top:160px;width:100%;text-align:center;font-size:18px}
.enq-mail{position:absolute;top:196px;width:100%;text-align:center;font-size:20px;color:var(--purple-dark)}
.enq-mail svg{vertical-align:-3px;margin:0 4px}

/* services */
.services{top:1438px;height:540px;background:linear-gradient(180deg,var(--purple) 0%,#7a63b0 45%,var(--purple-soft) 100%)}
.services h2{position:absolute;top:46px;width:100%;text-align:center;font-family:'Raleway',sans-serif;font-size:39px;color:var(--white)}
.service-card{position:absolute;top:120px;width:323px}
.service-card .photo{position:relative;width:323px;height:198px}
.service-card h3{margin-top:14px;font-family:'Raleway',sans-serif;font-size:26px;color:var(--purple-dark)}
.service-card p{margin-top:8px;font-size:14px;line-height:24px;color:#f3f0f8}
.service-card a{display:block;margin-top:8px;font-family:'Raleway',sans-serif;font-weight:700;font-size:16px;color:var(--purple-dark);text-decoration:none}

/* follow */
.follow{top:1978px;height:250px;background:var(--grey-bg)}
.follow .photo{left:40px;top:0;width:330px;height:220px;background:linear-gradient(120deg,#f1ddd2,#e2b9a4 60%,#efefef)}
.follow h2{position:absolute;top:36px;width:100%;text-align:center;font-family:'Raleway',sans-serif;font-weight:300;font-size:41px;color:#444}
.follow-logo{position:absolute;left:405px;top:98px;width:124px;height:124px;border-radius:50%;background:var(--white);border:1px solid #ddd;display:flex;align-items:center;justify-content:center;text-align:center;font-family:'Raleway',sans-serif;font-weight:700;font-size:15px;color:var(--purple);line-height:18px}
.follow-name{position:absolute;left:543px;top:110px;font-family:'Raleway',sans-serif;font-size:22px;color:var(--purple-dark)}
.follow-btn{position:absolute;left:545px;top:146px;width:203px;height:60px;border:2px solid var(--purple-dark);border-radius:4px;background:var(--white);display:flex;align-items:center;gap:12px;padding-left:6px;font-family:'Raleway',sans-serif;font-weight:600;font-size:19px;line-height:22px;color:var(--purple-dark)}
.follow-btn .sq{width:44px;height:44px;background:var(--purple-dark);border-radius:3px;flex:none}

/* partners */
.partners{top:2228px;height:192px;display:flex;align-items:center;justify-content:space-around;padding:0 70px}
.partner-badge{height:58px;border-radius:8px}
.badge-a{width:210px;background:linear-gradient(90deg,var(--badge-orange) 0 30%,var(--badge-blue) 30%)}
.badge-b{width:200px;background:var(--badge-blue);border-radius:29px}
.badge-c{width:170px;background:var(--badge-green)}
.badge-d{width:220px;height:10px;background:var(--badge-ink);border-radius:5px}

/* contact */
.contact{top:2420px;height:551px;background:linear-gradient(180deg,#5a5c4d 0%,#474a3c 40%,#3b3f35 100%)}
.contact h2{position:absolute;top:50px;width:100%;text-align:center;font-family:'Raleway',sans-serif;font-size:41px;color:var(--white)}
.field{position:absolute;left:77px;width:438px;height:50px;background:var(--white);border-radius:4px;font-size:14px;color:#999;padding:14px 18px}
.contact .btn-pill{left:77px;top:452px;width:165px;height:50px;font-weight:700;font-size:20px}
.contact .map{left:535px;top:157px;width:275px;height:278px;background:linear-gradient(135deg,#ecebe6,#dcdcd6)}
.addr{position:absolute;left:855px;top:160px;width:270px;color:var(--white);font-size:15px}
.addr h4{font-family:'Raleway',sans-serif;font-size:20px;margin-bottom:18px}
.addr-row{display:flex;gap:14px;margin-bottom:16px;line-height:22px}
.addr-row svg{flex:none;margin-top:2px}
.addr .circle{width:46px;height:46px;border-radius:50%;background:var(--white);margin-left:-6px;display:flex;align-items:center;justify-content:center}

/* footer */
.site-footer{top:2971px;height:54px;background:var(--purple);color:var(--white);font-size:15px;display:flex;align-items:center;justify-content:center}
</style>
</head>
<body>

<header class="section hero">
  <div class="photo" role="img" aria-label="Runner's legs and shoes on an open road at sunset"></div>
  <div class="brand"><span class="brand-dot"></span>Bramble Ridge Podiatry</div>
  <div class="hero-contact">
    <div><svg width="16" height="20" viewBox="0 0 16 20"><path d="M8 0a7 7 0 0 0-7 7c0 5 7 13 7 13s7-8 7-13a7 7 0 0 0-7-7zm0 10a3 3 0 1 1 0-6 3 3 0 0 1 0 6z" fill="#fff"/></svg>Suite 214 / 62 Harlow Street Eastvale 3100</div>
    <div><svg width="22" height="22" viewBox="0 0 24 24"><path d="M6.6 10.8a15 15 0 0 0 6.6 6.6l2.2-2.2c.3-.3.7-.4 1-.2 1.1.4 2.3.6 3.6.6.6 0 1 .4 1 1V20c0 .6-.4 1-1 1A17 17 0 0 1 3 4c0-.6.4-1 1-1h3.5c.6 0 1 .4 1 1 0 1.3.2 2.5.6 3.6.1.3 0 .7-.2 1z" fill="#fff"/></svg>CALL US NOW : <b>1300 482 905</b></div>
  </div>
  <h1 class="hero-title">Don't let pain run your life</h1>
  <div class="hero-rule"></div>
  <p class="hero-sub">Choose to be pain free</p>
  <a class="btn-book">BOOK AN APPOINTMENT</a>
</header>

<nav class="section main-nav">
  <a class="active">HOME</a><a>ABOUT</a><a>SERVICES</a><a>CONTACT</a>
</nav>

<section class="section welcome">
  <div class="photo" role="img" aria-label="Hand holding a sore heel"></div>
  <h1>WELCOME TO <span>BRAMBLE RIDGE PODIATRY</span></h1>
  <p class="p1">Bramble Ridge Podiatry is a Podiatry clinic in the heart of Eastvale CBD. We are located between Grey &amp; Marlow Streets in the Linden Business Centre / Harbourview Hotel Complex.</p>
  <p class="p2">Our podiatrists are fully qualified health professionals who are able to diagnose, treat, manage or help to prevent all medical conditions that affect the feet and lower limb.</p>
  <a class="btn-pill">READ MORE</a>
</section>

<section class="section enquiry">
  <div class="photo foot" role="img" aria-label="Grey footprint"></div>
  <div class="photo hands" role="img" aria-label="Hands massaging a foot"></div>
  <h2 class="enq-title">For Appointments or Enquiries</h2>
  <div class="enq-call">Please call us on
    <svg width="48" height="48" viewBox="0 0 48 48"><circle cx="24" cy="24" r="22" fill="none" stroke="#7cbb2b" stroke-width="2"/><path d="M18.5 21.5a12 12 0 0 0 8 8l2.5-2.5c.3-.3.7-.4 1-.2l3.5 1.2c.4.1.5.5.5.9V32c0 .5-.5 1-1 1A17 17 0 0 1 15 15c0-.5.5-1 1-1h3c.4 0 .8.1.9.5l1.2 3.5c.1.3 0 .7-.2 1z" fill="#7cbb2b"/></svg>
    <b>1300 482 905</b></div>
  <p class="enq-or">OR</p>
  <p class="enq-mail">Email: <svg width="20" height="16" viewBox="0 0 20 16"><rect x="1" y="1" width="18" height="14" fill="none" stroke="#452a7e" stroke-width="2"/><path d="M1 1l9 8 9-8" fill="none" stroke="#452a7e" stroke-width="2"/></svg>info@brambleridgepodiatry.net</p>
  <span class="notch"></span>
</section>

<section class="section services">
  <h2>SERVICES WE PROVIDE</h2>
  <article class="service-card" style="left:77px">
    <div class="photo" role="img" aria-label="Podiatrist treating a toenail with a medical device" style="background:linear-gradient(135deg,#8aa3b3,#d9dfe3 55%,#e8d0c4)"></div>
    <h3>General Treatment</h3>
    <p>Nails, Corns, Callus, Warts, Skin Disorders, Heel pain / Heel Spurs / Arch pain - Plantar Fasciitis</p>
    <a>READ MORE &raquo;</a>
  </article>
  <article class="service-card" style="left:440px">
    <div class="photo" role="img" aria-label="Sole of a foot being examined" style="background:linear-gradient(135deg,#e9e7e4,#dcc8bb 55%,#5aa59a)"></div>
    <h3>Specialised Treatments</h3>
    <p>Diabetic Management, Nail Surgery, Biomechanical Assessment, Gait Analysis, Orthotic Therapy</p>
    <a>READ MORE &raquo;</a>
  </article>
  <article class="service-card" style="left:800px">
    <div class="photo" role="img" aria-label="Bandaged ankle beside running shoes on a wooden floor" style="background:linear-gradient(135deg,#6b4a34,#a07656 50%,#4d8fc0)"></div>
    <h3>Sports Injury</h3>
    <p>Podiatrists are trained to diagnose and treat all medical conditions that affect the feet and lower limb.</p>
    <a>READ MORE &raquo;</a>
  </article>
</section>

<section class="section follow">
  <div class="photo" role="img" aria-label="Bare feet resting on tiptoe"></div>
  <h2>FOLLOW US</h2>
  <div class="follow-logo">Bramble<br>Ridge</div>
  <div class="follow-name">Bramble Ridge Podiatry</div>
  <a class="follow-btn"><span class="sq"></span><span>Like Us on<br>Our Page</span></a>
</section>

<section class="section partners" aria-label="Partner memberships">
  <span class="partner-badge badge-a"></span>
  <span class="partner-badge badge-b"></span>
  <span class="partner-badge badge-c"></span>
  <span class="partner-badge badge-d"></span>
</section>

<section class="section contact">
  <h2>CONTACT US</h2>
  <div class="field" style="top:157px">Name</div>
  <div class="field" style="top:214px">E-Mail</div>
  <div class="field" style="top:271px">Phone</div>
  <div class="field" style="top:328px;height:102px">Message</div>
  <a class="btn-pill">SUBMIT</a>
  <div class="photo map" role="img" aria-label="Street map showing the clinic location"></div>
  <div class="addr">
    <h4>CONTACT ADDRESS</h4>
    <div class="addr-row"><svg width="20" height="24" viewBox="0 0 16 20"><path d="M8 1a6 6 0 0 0-6 6c0 4.5 6 12 6 12s6-7.5 6-12a6 6 0 0 0-6-6zm0 8.5a2.5 2.5 0 1 1 0-5 2.5 2.5 0 0 1 0 5z" fill="none" stroke="#fff" stroke-width="1.4"/></svg><span>Suite 214 / 62 Harlow Street<br>Eastvale 3100.</span></div>
    <div class="addr-row"><svg width="20" height="20" viewBox="0 0 24 24"><path d="M6.6 10.8a15 15 0 0 0 6.6 6.6l2.2-2.2c.3-.3.7-.4 1-.2 1.1.4 2.3.6 3.6.6.6 0 1 .4 1 1V20c0 .6-.4 1-1 1A17 17 0 0 1 3 4c0-.6.4-1 1-1h3.5c.6 0 1 .4 1 1 0 1.3.2 2.5.6 3.6.1.3 0 .7-.2 1z" fill="#fff"/></svg><b>1300 482 905</b></div>
    <div class="addr-row"><svg width="20" height="16" viewBox="0 0 20 16"><rect x="1" y="1" width="18" height="14" fill="none" stroke="#fff" stroke-width="1.6"/><path d="M1 1l9 8 9-8" fill="none" stroke="#fff" stroke-width="1.6"/></svg>info@brambleridgepodiatry.net</div>
    <div class="circle"><svg width="18" height="18" viewBox="0 0 18 18"><path d="M3 9h11M9 4l5 5-5 5" fill="none" stroke="#553593" stroke-width="2.2" stroke-linecap="round" stroke-linejoin="round"/></svg></div>
  </div>
</section>

<footer class="section site-footer">© Bramble Ridge Podiatry- 2016. All Rights Reserved.</footer>

</body>
</html>
```